bamboo kettle vietnamese restaurant in need of a new menu

a family owned vietnamese restaurant in need of a new menu design that is fun, classy, and yet simple. menu that will catch the customers eyes. easy to read yet flows nicely. like to use the color green (basil green color) creme yellow and maroon. open to other colors as long as it looks nice together. our restaurant is family oriented, casual yet has a nice ambiance atmosphere.
prefer 11x17 portrait double sided. attached is our menu with the current price updated so use the info on this to start creating! looking for something unique, professional and one of a kind menu!
Updates
please use your own creative layout and design. we are open to ideas. the files uploaded are the updated prices and the logo is to use whichever one you feel goes with the menu.
Reason: don't see anything we like so far...please be creative!
Target Market(s)
restaurant consumers
Industry/Entity Type
Restaurant
Look and feel

```html
<!DOCTYPE html>
<html lang="en">
<head>
<meta charset="utf-8">
<title>Bamboo Kettle – Menu</title>
<link rel="stylesheet" href="https://fonts.googleapis.com/css2?family=Bebas+Neue&family=Oswald:wght@400;500&family=Roboto+Condensed:wght@400&display=swap">
<style>
:root{
  --basil:#6dbb45;
  --basil-soft:#a9d88a;
  --ink:#333333;
  --paper:#ffffff;
  --chili:#f26b21;
}
*{box-sizing:border-box;margin:0;padding:0}
html,body{width:1200px;height:777px;overflow:hidden;background:var(--paper)}
.menu{position:relative;width:1200px;height:777px;overflow:hidden;background:var(--paper);color:var(--ink);font-family:"Roboto Condensed",sans-serif}
.leaves{position:absolute;inset:0;width:1200px;height:777px}
.block{position:absolute}
.section-title{position:absolute;overflow:visible}
.section-title text{font-family:"Bebas Neue",sans-serif;fill:var(--basil)}
.section-sub{font-family:"Oswald",sans-serif;font-weight:400;text-transform:uppercase;line-height:1.05;color:var(--ink)}
.note{font-size:7.6px;text-transform:uppercase;line-height:1.25}
.item{display:grid;grid-template-columns:17px 1fr;margin-bottom:6px}
.num{font-family:"Oswald",sans-serif;font-size:10.5px;line-height:1.25}
.name{font-family:"Oswald",sans-serif;font-weight:500;font-size:10.5px;text-transform:uppercase;line-height:1.25}
.price{color:var(--basil);font-family:"Oswald",sans-serif;font-weight:400;font-style:italic;margin-left:3px}
.desc{font-size:7.6px;text-transform:uppercase;line-height:1.25;grid-column:2}
.desc .price{font-size:10.5px}
.desc em{font-style:italic}
.spicy{display:inline-block;width:7px;height:9px;margin-left:2px;vertical-align:-1px}
.extras{position:absolute;left:398px;top:346px;width:402px;height:118px;background:var(--basil)}
.extras ul{list-style:none;position:absolute;left:16px;top:6px;color:var(--paper);font-family:"Oswald",sans-serif;font-size:10.5px;line-height:11.7px;text-transform:uppercase}
.extras li::before{content:"•";margin-right:4px}
.extras .sub{font-family:"Roboto Condensed",sans-serif;font-size:9px;display:block;padding-left:10px}
.extras .val{font-family:"Roboto Condensed",sans-serif;font-style:italic}
.photo{position:absolute;border-radius:50%;border:3px solid var(--paper)}
.photo-pho{left:598px;top:342px;width:126px;height:126px;background:radial-gradient(circle at 45% 40%,#e7c7a6 0,#c98e62 28%,#b7a275 45%,#e8e1cf 62%,#f4f1e8 100%)}
.photo-rice{left:1072px;top:252px;width:106px;height:106px;background:radial-gradient(circle at 50% 45%,#e59a5a 0,#d88549 30%,#e9dcc6 60%,#f5f3ef 100%)}
</style>
</head>
<body>
<main class="menu">

<svg class="leaves" role="img" aria-label="Soft green watercolor leaves scattered around the menu edges" viewBox="0 0 1200 777">
  <defs>
    <radialGradient id="wash"><stop offset="0" stop-color="#cfe8bd" stop-opacity=".75"/><stop offset="1" stop-color="#e6f3dc" stop-opacity="0"/></radialGradient>
  </defs>
  <ellipse cx="60" cy="40" rx="150" ry="90" fill="url(#wash)"/>
  <ellipse cx="320" cy="30" rx="90" ry="60" fill="url(#wash)"/>
  <ellipse cx="1110" cy="90" rx="170" ry="140" fill="url(#wash)"/>
  <ellipse cx="1150" cy="420" rx="120" ry="200" fill="url(#wash)"/>
  <ellipse cx="70" cy="680" rx="150" ry="130" fill="url(#wash)"/>
  <ellipse cx="370" cy="560" rx="80" ry="110" fill="url(#wash)"/>
  <ellipse cx="720" cy="330" rx="90" ry="70" fill="url(#wash)"/>
  <ellipse cx="980" cy="560" rx="110" ry="80" fill="url(#wash)"/>
  <ellipse cx="820" cy="740" rx="100" ry="50" fill="url(#wash)"/>
</svg>

<svg width="0" height="0" style="position:absolute">
  <symbol id="flame" viewBox="0 0 10 13"><path d="M5 0C6 3 9 5 9 8.5A4 4 0 0 1 1 8.5C1 6 3 5 3.5 3 4.5 5 5 5 5 0Z" fill="#f26b21"/></symbol>
</svg>

<!-- Appetizers -->
<svg class="section-title" style="left:128px;top:24px" width="142" height="44"><text x="0" y="42" font-size="60" textLength="142" lengthAdjust="spacingAndGlyphs">APPETIZERS</text></svg>
<p class="block note" style="left:29px;top:74px;width:350px">Spring rolls (2) comes with lettuce, vermicelli noodles rolled in rice paper served with peanut sauce with choice of: (cannot be mixed):</p>

<div class="block" style="left:38px;top:106px;width:160px">
  <div class="item"><span class="num">1.</span><span class="name">Goi Cuon Tom &amp; Thit Heo<span class="price">4.50</span></span><span class="desc">Shrimp &amp; pork spring rolls</span></div>
  <div class="item"><span class="num">2.</span><span class="name">Goi Cuon Thit Heo / Ga / Or Bo Nuong<span class="price">5.50</span></span><span class="desc">Choice of: grilled pork / grilled chicken or grilled beef spring rolls</span></div>
  <div class="item"><span class="num">3.</span><span class="name">Bi Cuon<span class="price">4.50</span></span><span class="desc">Pork skin roasted with rice powder spring rolls</span></div>
  <div class="item"><span class="num">4.</span><span class="name">Cha Gio (2)<span class="price">4.50</span></span><span class="desc">Fried eggrolls with shrimp, pork &amp; vegetables rolled in egg wrap</span></div>
  <div class="item"><span class="num">5.</span><span class="name">Canh Ga Nuoc Mam (6)<span class="price">7.95</span></span><span class="desc">Fried chicken wings</span></div>
</div>
<div class="block" style="left:210px;top:106px;width:160px">
  <div class="item"><span class="num">6.</span><span class="name">Gio Tom (4)<span class="price">5.95</span></span><span class="desc">Fried shrimp rolls</span></div>
  <div class="item"><span class="num">7.</span><span class="name">Ca Vien Chien (8)<span class="price">4.95</span></span><span class="desc">Fried fish balls</span></div>
  <div class="item"><span class="num">8.</span><span class="name">Chao Tom (2)<span class="price">7.95</span></span><span class="desc">Grilled shrimp paste wrapped around sugar cane stick</span></div>
  <div class="item"><span class="num">9.</span><span class="name">Wonton Soup</span><span class="desc"><span class="price" style="margin:0">(cup) 4.95 (bowl) 7.50</span><br>Wonton shrimp &amp; pork soup</span></div>
  <div class="item"><span class="num">10.</span><span class="name">Tom Cua Soup</span><span class="desc"><span class="price" style="margin:0">(cup) 4.95 (bowl) 7.50</span><br>Crab meat, shrimp &amp; egg soup</span></div>
</div>

<p class="block note" style="left:29px;top:310px;width:350px">Vietnamese salad comes with thin cabbage, carrots, onions, mints, crushed peanuts tossed in lime juice &amp; vinegar with the following choices of:</p>
<div class="block" style="left:38px;top:336px;width:160px">
  <div class="item"><span class="num">11.</span><span class="name">Goi Ga<span class="price">8.95</span></span><span class="desc">Chicken salad</span></div>
  <div class="item"><span class="num">12.</span><span class="name">Goi Tom<span class="price">9.95</span></span><span class="desc">Shrimp salad</span></div>
</div>
<div class="block" style="left:210px;top:338px;width:160px">
  <div class="item"><span class="num">13.</span><span class="name">Bo Tai Chanh<span class="price">11.95</span></span><span class="desc">Rare thin sliced beef with onions, mints, basils, crushed peanuts in lime juice &amp; vinegar</span></div>
  <div class="item"><span class="num">14.</span><span class="name">Chim Cut Roti<span class="price">11.95</span></span><span class="desc">Roasted quails served with salt &amp; pepper</span></div>
</div>

<!-- Hu Tieu -->
<svg class="section-title" style="left:30px;top:412px" width="156" height="44"><text x="0" y="42" font-size="60" textLength="156" lengthAdjust="spacingAndGlyphs">HU TIEU (MI)</text></svg>
<p class="block section-sub" style="left:30px;top:456px;font-size:12px">Rice or egg noodle soup</p>
<p class="block note" style="left:30px;top:470px">In pork broth</p>
<div class="block" style="left:38px;top:485px;width:330px">
  <div class="item"><span class="num">15.</span><span class="name">Hu Tieu (Mi) Dac Biet<span class="price">10.50</span></span><span class="desc">Choice of: rice or egg noodle with shrimp, roast pork, chicken, imitation crab, quail eggs, ground pork &amp; fried shrimp cracker combination noodle soup</span></div>
  <div class="item"><span class="num">16.</span><span class="name">Hu Tieu (Mi) Hai San<span class="price">11.50</span></span><span class="desc">Choice of: rice or egg noodle with shrimp, scallop, squid, fish balls &amp; imitation crab seafood noodle soup</span></div>
  <div class="item"><span class="num">17.</span><span class="name">Hu Tieu Mytho<span class="price">9.95</span></span><span class="desc">Shrimp, roast pork, chicken, fish ball, imitation crab &amp; ground pork with clear noodle soup</span></div>
  <div class="item"><span class="num">18.</span><span class="name">Hu Tieu Sate<span class="price">9.50</span><svg class="spicy"><use href="#flame"/></svg></span><span class="desc">Beef with tomato slices, cucumber, bean sprouts &amp; crushed peanuts in spicy noodle soup</span></div>
</div>
<div class="block" style="left:38px;top:650px;width:165px">
  <div class="item"><span class="num">19.</span><span class="name">Hu Tieu (Mi) Kho Dac Biet<span class="price">10.95</span></span><span class="desc">Choice of: rice or egg noodle with shrimp, roast pork, chicken, imitation crab, ground pork and fried shrimp cracker with soup on the side</span></div>
  <div class="item"><span class="num">20.</span><span class="name">Mi Hoanh Thanh<span class="price">8.95</span></span><span class="desc">Wonton with egg noodle soup<br><span class="name" style="font-size:10px">+Xa Xiu (roast pork)</span><span class="price">9.95</span></span></div>
</div>
<div class="block" style="left:210px;top:650px;width:160px">
  <div class="item"><span class="num">21.</span><span class="name">Banh Canh Tom Thit Gio Heo<span class="price">9.50</span></span><span class="desc">Shrimp, pork knuckle &amp; vietnamese big noodle soup</span></div>
  <div class="item"><span class="num">22.</span><span class="name">Banh Canh Ga<span class="price">8.95</span></span><span class="desc">Chicken with vietnamese big noodle soup</span></div>
</div>

<!-- Pho -->
<svg class="section-title" style="left:578px;top:24px" width="46" height="44"><text x="0" y="42" font-size="60" textLength="46" lengthAdjust="spacingAndGlyphs">PHO</text></svg>
<p class="block section-sub" style="left:500px;top:68px;width:200px;text-align:center;font-size:13px">Rice noodles soup</p>
<div class="block" style="left:438px;top:106px;width:165px">
  <div class="item"><span class="num">23.</span><span class="name">Pho Dac Biet<span class="price">9.50</span></span><span class="desc">Steak, brisket, flank, tendon, tripe &amp; meatballs combination noodle soup</span></div>
  <div class="item"><span class="num">24.</span><span class="name">Pho<span class="price">8.50</span></span><span class="desc">Noodle soup with choices up to 3 items: <em>steak, brisket, flank, tendon, tripe, meatball or vegetables</em></span></div>
  <div class="item"><span class="num">25.</span><span class="name">Pho Ga Vietnam (Ga Di Bo)<span class="price">10.50</span></span><span class="desc">Free range chicken noodle soup</span></div>
  <div class="item"><span class="num">26.</span><span class="name">Pho Ga My<span class="price">9.50</span></span><span class="desc">White chicken &amp; mixed vegetables noodle soup</span></div>
  <div class="item"><span class="num">27.</span><span class="name">Pho Thit Heo / Bo / Or Ga Nuong<span class="price">10.50</span></span><span class="desc">Choice of: grilled pork, grilled beef or grilled chicken with mixed vegetables noodle soup</span></div>
</div>
<div class="block" style="left:610px;top:106px;width:170px">
  <div class="item"><span class="num">28.</span><span class="name">Pho Do Bien<span class="price">11.50</span></span><span class="desc">Shrimp, scallop, squid, fish balls, imitation crab &amp; vegetables seafood noodle soup</span></div>
  <div class="item"><span class="num">29.</span><span class="name">Pho Tom<span class="price">9.95</span></span><span class="desc">Shrimp with mixed vegetables noodle soup</span></div>
  <div class="item"><span class="num">30.</span><span class="name">Pho Do Bien Chua Cay<span class="price">11.50</span><svg class="spicy"><use href="#flame"/></svg></span><span class="desc">Shrimp, scallop, squid, fish balls &amp; imitation crab in hot &amp; sour seafood noodle soup</span></div>
  <div class="item"><span class="num">31.</span><span class="name">Pho Tre Em<span class="price">7.50</span></span><span class="desc">Kid's steak &amp; meatball noodle soup</span></div>
</div>

<div class="extras">
  <ul>
    <li>X-Large <span class="val">2.00 more</span></li>
    <li>Extra meat <span class="val">(steak, chicken, etc.) 3.50</span></li>
    <li>Extra shrimp <span class="val">3.00</span></li>
    <li>Extra herbs or vegetables <span class="val">1.50</span><span class="sub">(ex: cilantros, basils, beansprouts, etc.)</span></li>
    <li>Extra rice, soup or noodles <span class="val">1.50</span></li>
    <li>Change noodle or brown rice <span class="val">2.00</span></li>
    <li>Add fried egg <span class="val">1.50</span></li>
    <li>Add or change to fried rice <span class="val">3.00</span></li>
  </ul>
</div>
<div class="photo photo-pho" role="img" aria-label="Photo of a bowl of pho with beef slices, herbs and broth"></div>

<!-- Bun -->
<svg class="section-title" style="left:413px;top:476px" width="45" height="41"><text x="0" y="39" font-size="56" textLength="45" lengthAdjust="spacingAndGlyphs">BUN</text></svg>
<p class="block section-sub" style="left:462px;top:477px;font-size:13px">Vermicelli noodle bowl</p>
<p class="block note" style="left:462px;top:493px;width:330px;font-size:8.4px">All vermicelli bowl comes with fresh lettuce, bean sprouts, sliced cucumbers, shredded carrots &amp; crushed peanuts</p>
<div class="block" style="left:438px;top:535px;width:165px">
  <div class="item"><span class="num">32.</span><span class="name">Bun Dac Biet<span class="price">12.95</span></span><span class="desc">Choice of: grilled pork, grilled chicken or grilled beef with grilled shrimp &amp; fried eggroll special combination vermicelli bowl</span></div>
  <div class="item"><span class="num">33.</span><span class="name">Bun - Vermicelli Bowl<span class="price">9.50</span></span><span class="desc">Choice of: grilled pork, grilled chicken or grilled beef<br><span class="name" style="font-size:10px">+ Eggroll</span><span class="price">9.95</span><br><span class="name" style="font-size:10px">+ Shrimp</span><span class="price">10.50</span></span></div>
  <div class="item"><span class="num">34.</span><span class="name">Bun Tom Nuong (8)<span class="price">10.95</span></span><span class="desc">Grilled shrimp vermicelli bowl</span></div>
</div>
<div class="block" style="left:610px;top:535px;width:170px">
  <div class="item"><span class="num">35.</span><span class="name">Bun Cha Gio (3)<span class="price">9.50</span></span><span class="desc">Fried eggroll vermicelli bowl</span></div>
  <div class="item"><span class="num">36.</span><span class="name">Bun Chao Tom (2)<span class="price">9.50</span></span><span class="desc">Grilled shrimp paste vermicelli bowl</span></div>
  <div class="item"><span class="num">37.</span><span class="name">Bun Bo Hue<span class="price">9.50</span><svg class="spicy"><use href="#flame"/></svg></span><span class="desc">Spicy beef noodle soup with beef shank, pork knuckle, pork blood with large vermicelli noodles</span></div>
  <div class="item"><span class="num">38.</span><span class="name">Bun Rieu<span class="price">9.50</span></span><span class="desc">Mixed ground pork &amp; crab, pork blood, dried tofu with vermicelli rice noodle in tomato broth soup</span></div>
  <div class="item"><span class="num">39.</span><span class="name">Bun Mang Vit<span class="price">9.50</span></span><span class="desc">Duck &amp; bamboo vermicelli noodle soup</span></div>
</div>

<!-- Com Tam -->
<svg class="section-title" style="left:944px;top:24px" width="110" height="44"><text x="0" y="42" font-size="60" textLength="110" lengthAdjust="spacingAndGlyphs">COM TAM</text></svg>
<p class="block section-sub" style="left:900px;top:68px;width:200px;text-align:center;font-size:13px">Broken rice plate</p>
<div class="block" style="left:836px;top:97px;width:320px">
  <div class="item"><span class="num">40.</span><span class="name">Com Dac Biet<span class="price">14.95</span></span><span class="desc">Special rice combination with grilled chicken, grilled pork, grilled shrimp &amp; fried eggroll</span></div>
  <div class="item"><span class="num">41.</span><span class="name">Com Suon Nuong Xa<span class="price">9.95</span></span><span class="desc">Grilled pork chops marinated in lemongrass</span></div>
  <div class="item"><span class="num">42.</span><span class="name">Com Suon Bi Cha<span class="price">9.50</span></span><span class="desc">Grilled pork chop, pork skin roasted with rice powder &amp; eggcake</span></div>
  <div class="item"><span class="num">43.</span><span class="name">Com Thit Nuong, Ga Nuong or Bo Nuong<span class="price">9.75</span></span><span class="desc" style="width:210px">Choice of: grilled pork, grilled chicken or grilled beef<br><span class="name" style="font-size:10px">+Shrimp</span><span class="price">10.95</span></span></div>
  <div class="item"><span class="num">44.</span><span class="name">Com Suon Dai Han<span class="price">13.95</span></span><span class="desc">Grilled korean bbq ribs</span></div>
</div>
<div class="photo photo-rice" role="img" aria-label="Photo of a plate of fried rice"></div>

<!-- Com Chien -->
<svg class="section-title" style="left:810px;top:318px" width="126" height="44"><text x="0" y="42" font-size="60" textLength="126" lengthAdjust="spacingAndGlyphs">COM CHIEN</text></svg>
<p class="block section-sub" style="left:940px;top:320px;font-size:13px">Fried rice</p>
<p class="block note" style="left:940px;top:336px;width:110px;color:var(--basil-soft);font-size:8.4px">Fried rice is cooked with egg, peas &amp; carrots</p>
<div class="block" style="left:836px;top:375px;width:160px">
  <div class="item"><span class="num">45.</span><span class="name">Com Chien Thap Cam<span class="price">10.95</span></span><span class="desc">House special fried rice with shrimp, roasted pork, sausage with peas &amp; carrots</span></div>
  <div class="item"><span class="num">46.</span><span class="name">Com Chien Tom<span class="price">9.95</span></span><span class="desc">Shrimp fried rice</span></div>
  <div class="item"><span class="num">47.</span><span class="name">Com Chien Ga<span class="price">9.95</span></span><span class="desc">Chicken fried rice</span></div>
</div>
<div class="block" style="left:1006px;top:375px;width:175px">
  <div class="item"><span class="num">48.</span><span class="name">Com Chien Canh Ga<span class="price">9.50</span></span><span class="desc">Fried rice with fried chicken wings</span></div>
  <div class="item"><span class="num">49.</span><span class="name">Com Chien Bo Luc Lac<span class="price">14.50</span></span><span class="desc">(Shaking beef) stir fry filet mignon with bell peppers with fried rice<br><span class="name" style="font-size:10px">+ Shrimp</span><span class="price">16.95</span></span></div>
</div>

<!-- Xao -->
<svg class="section-title" style="left:810px;top:496px" width="42" height="42"><text x="0" y="40" font-size="57" textLength="42" lengthAdjust="spacingAndGlyphs">XAO</text></svg>
<p class="block section-sub" style="left:855px;top:497px;font-size:12.5px;line-height:13.5px">Stir fry<br>with rice<br>plate</p>
<div class="block" style="left:836px;top:550px;width:165px">
  <div class="item"><span class="num">50.</span><span class="name">Ga Xao Gung<span class="price">10.95</span></span><span class="desc">Stir fry chicken with ginger</span></div>
  <div class="item"><span class="num">51.</span><span class="name">Ga or Bo Xao Xa Ot<span class="price">10.95</span><svg class="spicy"><use href="#flame"/></svg></span><span class="desc">Choice of: stir fry chicken or beef in hot chili &amp; lemongrass</span></div>
  <div class="item"><span class="num">52.</span><span class="name">Tom Xao Xa Ot<span class="price">11.95</span><svg class="spicy"><use href="#flame"/></svg></span><span class="desc">Stir fry shrimp in hot chilli &amp; lemongrass</span></div>
  <div class="item"><span class="num">53.</span><span class="name">Ga or Bo Xao Rau Cai<span class="price">10.95</span></span><span class="desc">Choice of: stir fry chicken or beef with mixed vegetables</span></div>
  <div class="item"><span class="num">54.</span><span class="name">Tom Xao Rau Cai<span class="price">11.95</span></span><span class="desc">Stir fry shrimp with mixed vegetables</span></div>
</div>
<div class="block" style="left:1006px;top:550px;width:180px">
  <div class="item"><span class="num">55.</span><span class="name">Mi Xao Mem or Don Hai San<span class="price">15.95</span></span><span class="desc">Choice of: soft or crispy noodles stir fry with shrimp, squid, fish ball &amp; imitation crab with vegetables</span></div>
  <div class="item"><span class="num">56.</span><span class="name">Com Tom Rang Chay Mo<span class="price">12.95</span></span><span class="desc">Stir fry shrimp, ginger, onion &amp; bell pepper in garlic sauce</span></div>
  <div class="item"><span class="num">57.</span><span class="name">Canh Chua Ca or Tom<span class="price">15.95</span></span><span class="desc">Choice of: fish or shrimp soup with tomato, pineapple, okra &amp; bean sprouts served with white rice (serving 2-4)</span></div>
  <div class="item"><span class="num">58.</span><span class="name">Ca Kho To<span class="price">15.95</span></span><span class="desc">Braised swai fish in clay pot with black pepper &amp; dry shallots served with white rice</span></div>
</div>

</main>
</body>
</html>
```